Executive Business Card for Healthcare Company [Need Today]

I need a business card design for a healthcare company. The only branding the company has thus far is a logo. The cards will be utilized by company executives. The design I envision will be vibrant and appealing but with a corporate feel. They shouldn't be too casual or playful. I would like to complete this project TODAY if possible.

Target Market(s)

Healthcare vendors, other executives in healthcare and pharmaceuticals

Industry/Entity Type

Pharmaceutical

Contact Information for Business Card

See attachment

Font styles to use
Serif
Sans Serif

Colors

Designer to choose colors to be used in the design.

```html
<!DOCTYPE html>
<html lang="en">
<head>
<meta charset="utf-8">
<title>Corven Therapeutics – Business Card</title>
<link href="https://fonts.googleapis.com/css2?family=Roboto:wght@300;400;500&display=swap" rel="stylesheet">
<style>
  :root {
    --backdrop: #3b3b3d;
    --card: #222224;
    --teal: #22b3c3;
    --green: #3dbb94;
    --text-light: #e6e6e6;
    --text-muted: #bdbdbd;
  }
  * { box-sizing: border-box; margin: 0; padding: 0; }
  html, body {
    width: 799px; height: 1200px; overflow: hidden;
    background: var(--backdrop);
    font-family: "Roboto", Arial, sans-serif;
  }
  .canvas {
    position: relative; width: 799px; height: 1200px;
  }
  .card {
    position: absolute; left: 60px;
    width: 680px; height: 389px;
    background: var(--card);
    border-radius: 4px;
    overflow: hidden;
    box-shadow: 0 12px 30px rgba(0,0,0,.45);
  }
  .card--front { top: 150px; }
  .card--back { top: 650px; }

  /* Front */
  .front-brand {
    position: absolute; left: 110px; top: 120px;
    display: flex; align-items: center; gap: 28px;
  }
  .brand-ring {
    width: 104px; height: 104px; border-radius: 50%;
    border: 4px solid var(--green);
    flex: none;
  }
  .brand-name {
    color: var(--teal); font-weight: 300;
    font-size: 46px; line-height: 1.05; letter-spacing: 1px;
    text-transform: lowercase;
  }
  .brand-name span { display: block; }
  .front-web {
    position: absolute; left: 0; right: 0; bottom: 56px;
    text-align: center; color: var(--text-light);
    font-size: 17px; letter-spacing: 4px; font-weight: 400;
  }

  /* Back */
  .back-brand {
    position: absolute; left: 70px; top: 34px;
    color: var(--teal); font-weight: 300;
    font-size: 40px; line-height: 1.05; letter-spacing: 1px;
    text-transform: lowercase;
  }
  .back-brand span { display: block; }
  .edge-tab {
    position: absolute; left: -22px; top: 140px;
    width: 40px; height: 40px; border-radius: 50%;
    background: var(--teal);
  }
  .contact {
    position: absolute; left: 34px; top: 140px;
    color: var(--text-light);
  }
  .contact-name {
    color: var(--teal); font-size: 24px; font-weight: 400;
  }
  .contact-title {
    font-size: 12px; color: var(--text-muted); margin: 4px 0 18px;
  }
  .contact-list { list-style: none; font-size: 15px; }
  .contact-list li {
    display: flex; align-items: center; gap: 8px; margin-bottom: 7px;
  }
  .contact-list svg { width: 14px; height: 14px; fill: var(--teal); flex: none; }
  .contact-address { font-size: 15px; margin-top: 2px; }
  .back-ring {
    position: absolute; left: 420px; top: 70px;
    width: 300px; height: 300px; border-radius: 50%;
    border: 6px solid var(--green);
  }
</style>
</head>
<body>
<main class="canvas">

  <section class="card card--front" aria-label="Business card front">
    <div class="front-brand">
      <div class="brand-ring"></div>
      <div class="brand-name"><span>corven</span><span>therapeutics</span></div>
    </div>
    <p class="front-web">www.corvenrx.com</p>
  </section>

  <section class="card card--back" aria-label="Business card back">
    <div class="back-brand"><span>corven</span><span>therapeutics</span></div>
    <div class="edge-tab"></div>
    <div class="contact">
      <h1 class="contact-name">Daniel Hartley</h1>
      <p class="contact-title">Senior Director of Marketing</p>
      <ul class="contact-list">
        <li>
          <svg viewBox="0 0 24 24" aria-hidden="true"><path d="M6.6 10.8a15 15 0 0 0 6.6 6.6l2.2-2.2c.3-.3.7-.4 1-.2 1.1.4 2.3.6 3.6.6.6 0 1 .4 1 1V20c0 .6-.4 1-1 1A17 17 0 0 1 3 4c0-.6.4-1 1-1h3.5c.6 0 1 .4 1 1 0 1.3.2 2.5.6 3.6.1.3 0 .7-.2 1z"/></svg>
          555-201-4482
        </li>
        <li>
          <svg viewBox="0 0 24 24" aria-hidden="true"><path d="M7 1h10a2 2 0 0 1 2 2v18a2 2 0 0 1-2 2H7a2 2 0 0 1-2-2V3a2 2 0 0 1 2-2zm0 3v14h10V4zm5 15.5a1 1 0 1 0 0 2 1 1 0 0 0 0-2z"/></svg>
          555-318-7760
        </li>
        <li>
          <svg viewBox="0 0 24 24" aria-hidden="true"><path d="M12 2a10 10 0 1 0 0 20 10 10 0 0 0 0-20zm6.9 6h-3a15 15 0 0 0-1.3-3.9A8 8 0 0 1 18.9 8zM12 4c.8 1.2 1.5 2.5 1.9 4h-3.8c.4-1.5 1.1-2.8 1.9-4zM4.3 14a8 8 0 0 1 0-4h3.4a16 16 0 0 0 0 4zm.8 2h3a15 15 0 0 0 1.3 3.9A8 8 0 0 1 5.1 16zm3-8h-3a8 8 0 0 1 4.3-3.9C8.8 5.3 8.4 6.6 8.1 8zM12 20c-.8-1.2-1.5-2.5-1.9-4h3.8c-.4 1.5-1.1 2.8-1.9 4zm2.3-6H9.7a14 14 0 0 1 0-4h4.6a14 14 0 0 1 0 4zm.3 5.9c.6-1.2 1-2.5 1.3-3.9h3a8 8 0 0 1-4.3 3.9zm1.7-5.9a16 16 0 0 0 0-4h3.4a8 8 0 0 1 0 4z"/></svg>
          dhartley@corvenrx.com
        </li>
      </ul>
      <p class="contact-address">118 W Laurel Avenue Fairview, GA 30999</p>
    </div>
    <div class="back-ring"></div>
  </section>

</main>
</body>
</html>
```